Telecommunications/Power civil contractor needs business card design

Were a new telecommunications/power underground civil contractor that is looking for a new business card design. Our company colours are silver or grey and orange. Feel free to use the white background logo or the black background logo.

Target Market(s)

Local contractors, utility companies, private sector mining/energy companies, developers.

Industry/Entity Type

Telecommunications

Contact Information for Business Card

Each card will need the following info:
Persons name:
Title:
E-mail:
Phone number:
Shop Address:
Mailing Address:

Requirements
Must have
• Each card will need the following info:
• Persons name:
• Title:
• E-mail:
• Phone number:
• Shop Address:
• Mailing Address:

```html
<!DOCTYPE html>
<html lang="en">
<head>
<meta charset="utf-8">
<title>Ridgeline Contracting Inc – Business Card</title>
<link rel="stylesheet" href="https://fonts.googleapis.com/css2?family=Arimo:wght@400;700&family=Tinos:wght@700&display=swap">
<style>
  :root {
    --backdrop: #2b2b2b;
    --card-black: #050505;
    --card-black-soft: #151515;
    --card-grey: #6e6e6e;
    --card-grey-light: #7c7c7c;
    --divider: #8d8d8d;
    --ink: #141414;
    --orange: #e8652a;
    --silver: #9a9a9a;
  }
  * { margin: 0; padding: 0; box-sizing: border-box; }
  html, body { width: 1200px; height: 997px; overflow: hidden; }
  body {
    background: var(--backdrop);
    font-family: "Arimo", Arial, sans-serif;
    position: relative;
  }
  .card {
    position: absolute;
    left: 250px;
    width: 700px;
    height: 400px;
    border-radius: 22px;
    overflow: hidden;
    box-shadow: 0 10px 30px rgba(0,0,0,.5);
  }
  .card--back {
    top: 58px;
    background: linear-gradient(160deg, var(--card-black-soft), var(--card-black) 70%);
    display: flex;
    align-items: center;
    justify-content: center;
  }
  .card--front {
    top: 528px;
    background: linear-gradient(180deg, var(--card-grey-light), var(--card-grey));
  }
  .brand {
    display: flex;
    align-items: center;
    gap: 16px;
    color: var(--orange);
    font-family: "Arimo", Arial, sans-serif;
    font-weight: 700;
    letter-spacing: 1px;
    text-transform: uppercase;
  }
  .brand__circle {
    border: 5px solid var(--orange);
    border-radius: 50%;
    flex: none;
  }
  .card--back .brand { font-size: 36px; }
  .card--back .brand__circle { width: 70px; height: 70px; }
  .front__top {
    position: absolute;
    inset: 0 0 auto 0;
    height: 196px;
    background: var(--card-black);
  }
  .front__divider {
    position: absolute;
    left: 0; right: 0;
    top: 196px;
    height: 16px;
    background: var(--card-black-soft);
    border-top: 3px solid var(--divider);
  }
  .front__notch {
    position: absolute;
    left: 36px;
    top: 212px;
    width: 0; height: 0;
    border-left: 7px solid transparent;
    border-right: 7px solid transparent;
    border-top: 9px solid var(--card-black-soft);
  }
  .front__logo {
    position: absolute;
    left: 220px;
    top: 50px;
    width: 280px;
    height: 150px;
    background: var(--card-black);
    display: flex;
    align-items: center;
    justify-content: center;
  }
  .front__logo .brand { font-size: 22px; gap: 12px; }
  .front__logo .brand__circle { width: 46px; height: 46px; border-width: 4px; }
  .person {
    position: absolute;
    left: 36px;
    top: 228px;
    color: var(--ink);
  }
  .person__name { font-size: 26px; font-weight: 400; }
  .person__title {
    font-family: "Tinos", "Times New Roman", serif;
    font-weight: 700;
    font-size: 16px;
    margin-top: 4px;
  }
  .contact {
    position: absolute;
    left: 36px;
    bottom: 34px;
    list-style: none;
    color: var(--ink);
    font-size: 17px;
  }
  .contact li { display: flex; align-items: center; gap: 12px; margin-top: 12px; }
  .contact svg, .address svg { width: 18px; height: 18px; fill: var(--ink); flex: none; }
  .address {
    position: absolute;
    right: 36px;
    top: 222px;
    list-style: none;
    color: var(--ink);
    text-align: right;
    font-size: 16px;
  }
  .address li { display: flex; justify-content: flex-end; align-items: center; gap: 10px; margin-bottom: 10px; min-height: 20px; }
  .address .address__company { font-size: 18px; }
  .address .icon-slot { width: 18px; flex: none; }
</style>
</head>
<body>

  <section class="card card--back" aria-label="Card back">
    <div class="brand"><span class="brand__circle"></span><span>Ridgeline Contracting Inc</span></div>
  </section>

  <section class="card card--front" aria-label="Card front">
    <div class="front__top"></div>
    <div class="front__divider"></div>
    <div class="front__notch"></div>

    <div class="front__logo">
      <div class="brand"><span class="brand__circle"></span><span>Ridgeline Contracting Inc</span></div>
    </div>

    <div class="person">
      <h1 class="person__name">Mason Whitfield</h1>
      <p class="person__title">Owner</p>
    </div>

    <ul class="contact">
      <li>
        <svg viewBox="0 0 24 24" aria-hidden="true"><path d="M6.6 10.8a15.1 15.1 0 0 0 6.6 6.6l2.2-2.2a1 1 0 0 1 1-.25 11.4 11.4 0 0 0 3.6.57 1 1 0 0 1 1 1V20a1 1 0 0 1-1 1A17 17 0 0 1 3 4a1 1 0 0 1 1-1h3.5a1 1 0 0 1 1 1c0 1.25.2 2.45.57 3.57a1 1 0 0 1-.25 1z"/></svg>
        <span>0400 555 182</span>
      </li>
      <li>
        <svg viewBox="0 0 24 24" aria-hidden="true"><path d="M2 5h20v14H2z" fill="none"/><path d="M3 5h18a1 1 0 0 1 1 1v12a1 1 0 0 1-1 1H3a1 1 0 0 1-1-1V6a1 1 0 0 1 1-1zm9 7 8-5H4z"/></svg>
        <span>mason@ridgelinecontracting.com</span>
      </li>
    </ul>

    <ul class="address">
      <li class="address__company">
        <span>Ridgeline Contracting inc.</span>
        <svg viewBox="0 0 24 24" aria-hidden="true"><path d="M12 3 2 12h3v8h5v-5h4v5h5v-8h3z"/></svg>
      </li>
      <li>
        <span>Shop no 42, sec 11, Fairview</span>
        <svg viewBox="0 0 24 24" aria-hidden="true"><path d="M12 2a7 7 0 0 0-7 7c0 5.2 7 13 7 13s7-7.8 7-13a7 7 0 0 0-7-7zm0 9.5A2.5 2.5 0 1 1 12 6.5a2.5 2.5 0 0 1 0 5z"/></svg>
      </li>
      <li>
        <span>18 Cedar Brook Lane, Alden, CT 06000</span>
        <span class="icon-slot"></span>
      </li>
    </ul>
  </section>

</body>
</html>
```